first fantastic look and impression

We are looking for a concept for letterhead, business card, emailfooter and template for invoices or offers for our company in the consultation business.
The dancer is a symbol who we are: it looks simple, but there is a lot of hard work and many years of training in this movement. The look is also what we want: elegant, modern, strong, with a touch of extravaganza
Target Market(s)
Hotelbusiness , Consulting
Font styles to use
Sans Serif
Other font styles liked:
- please give us a option we are open
Requirements
Must have
- We are not typical consultants but sparring partners and coaches for the hotel and that should also be expressed in the design. Maybe there is an icon that supports the whole thing. We are more modern and bolder than our industry colleagues.
we are modern, fresh, agile, fast
Nice to have
- a icon

```html
<!DOCTYPE html>
<html lang="en">
<head>
<meta charset="utf-8">
<title>Business Card – Front and Back</title>
<link href="https://fonts.googleapis.com/css2?family=Khand:wght@600&family=Roboto:wght@300;400&display=swap" rel="stylesheet">
<style>
  :root {
    --backdrop: #6e6e6e;
    --card: #161616;
    --card-edge: #1c1c1c;
    --ink-light: #d9d9d9;
    --ink-soft: #bdbdbd;
    --band: #c9c9c9;
    --band-ink: #1a1a1a;
    --figure-a: #2a2a2a;
    --figure-b: #1b1b1b;
  }
  html, body {
    margin: 0;
    padding: 0;
    width: 1200px;
    height: 1138px;
    overflow: hidden;
    background: var(--backdrop);
  }
  .canvas {
    position: relative;
    width: 1200px;
    height: 1138px;
    font-family: "Roboto", sans-serif;
  }
  .card {
    position: absolute;
    width: 620px;
    height: 374px;
    border-radius: 16px;
    background: linear-gradient(160deg, var(--card-edge), var(--card));
    overflow: hidden;
  }
  .card--front { left: 274px; top: 186px; }
  .card--back  { left: 276px; top: 608px; }

  .dancer-figure {
    position: absolute;
    left: 162px;
    top: 57px;
    width: 302px;
    height: 282px;
    border-radius: 46% 54% 50% 50% / 52% 48% 52% 48%;
    background: radial-gradient(ellipse at 55% 40%, var(--figure-a), var(--figure-b) 72%);
  }

  .brand-name {
    position: absolute;
    left: 88px;
    top: 136px;
    width: 200px;
    text-align: center;
    font-family: "Roboto", sans-serif;
    font-weight: 300;
    font-size: 46px;
    line-height: 64px;
    letter-spacing: 1px;
    color: var(--ink-light);
  }

  .contact {
    position: absolute;
    left: 360px;
    top: 66px;
    color: var(--ink-soft);
  }
  .contact__name {
    margin: 0;
    font-family: "Khand", sans-serif;
    font-weight: 600;
    font-size: 27px;
    line-height: 30px;
    color: var(--ink-light);
  }
  .contact__role {
    margin: 0 0 22px;
    font-size: 16px;
    line-height: 22px;
  }
  .contact__list {
    list-style: none;
    margin: 0;
    padding: 0;
  }
  .contact__item {
    display: flex;
    align-items: center;
    height: 24px;
    font-size: 16px;
  }
  .contact__icon {
    width: 14px;
    height: 14px;
    margin-right: 18px;
    fill: none;
    stroke: var(--ink-soft);
    stroke-width: 1.4;
  }
  .contact__address {
    margin: 6px 0 0 4px;
    font-size: 16px;
    line-height: 24px;
    font-style: normal;
  }

  .tagline-band {
    position: absolute;
    left: 0;
    bottom: 0;
    width: 620px;
    height: 46px;
  }
  .tagline-band svg { position: absolute; inset: 0; }
  .tagline {
    position: absolute;
    left: 360px;
    top: 0;
    margin: 0;
    line-height: 46px;
    font-size: 16px;
    color: var(--band-ink);
  }
</style>
</head>
<body>
<div class="canvas">

  <section class="card card--front">
    <div class="dancer-figure" role="img" aria-label="Embossed line illustration of a leaping dancer holding a flowing veil"></div>
  </section>

  <section class="card card--back">
    <div class="brand-name">Vantora</div>

    <div class="contact">
      <h1 class="contact__name">John Doe Smith</h1>
      <p class="contact__role">Managing Director</p>
      <ul class="contact__list">
        <li class="contact__item">
          <svg class="contact__icon" viewBox="0 0 14 14" aria-hidden="true"><path d="M2 5c0-2 2-3 5-3s5 1 5 3l-2 1-1-2H5L4 6z"/><rect x="3" y="7" width="8" height="5" rx="1"/></svg>
          828-111-1111
        </li>
        <li class="contact__item">
          <svg class="contact__icon" viewBox="0 0 14 14" aria-hidden="true"><rect x="1" y="3" width="12" height="8"/><path d="M1 3l6 5 6-5"/></svg>
          john@yourwebsite.com
        </li>
        <li class="contact__item">
          <svg class="contact__icon" viewBox="0 0 14 14" aria-hidden="true"><circle cx="7" cy="7" r="6"/><ellipse cx="7" cy="7" rx="2.6" ry="6"/><path d="M1 7h12"/></svg>
          www.yourwebsite.com
        </li>
      </ul>
      <address class="contact__address">234 Anywhere St., Any City,<br>Any Town, US 123456</address>
    </div>

    <div class="tagline-band">
      <svg width="620" height="46" viewBox="0 0 620 46" aria-hidden="true">
        <path d="M300 0 H620 V46 H276 L292 6 Q295 0 300 0 Z" fill="var(--band)"/>
      </svg>
      <p class="tagline">Elegant and Fasion</p>
    </div>
  </section>

</div>
</body>
</html>
```